New business blog needs wordpress theme

I need a unique wordpress theme for my new business oriented blog at hollowpeakdesk.com. The blog focuses on my experience as an entrepreneur and offers insights into business problems while chronicling my experience building a new company.

I would like to see a theme that looks more like a creative professional's website, not a business website. Large photos, bright colors, unique layout. I do not want stock photos of people in suits doing business type things. Also, no pictures of me - I am blogging anonymously.

The design should communicate technology and beauty - for example, I really like the feel of the landing page at www.tundrelo.com - it is beautiful to look at but also reflects the cutting edge nature of what they are doing.

Industry/Entity Type

Business

```html
<!DOCTYPE html>
<html lang="en">
<head>
<meta charset="utf-8">
<title>Hollow Peak Desk</title>
<link href="https://fonts.googleapis.com/css2?family=Open+Sans:wght@400;600&family=Ubuntu:wght@400&display=swap" rel="stylesheet">
<style>
:root{
  --blue:#2a86c8;
  --blue-dark:#1f6fa8;
  --red:#f0524a;
  --red-dark:#d9433b;
  --ink:#333;
  --muted:#666;
  --link:#2a86c8;
  --page:#e9e9e9;
  --card:#fff;
  --line:#ddd;
  --footer:#222;
  --star:#ffe01a;
}
*{box-sizing:border-box;margin:0;padding:0}
html,body{width:730px;height:1200px;overflow:hidden}
body{font-family:"Open Sans",Arial,sans-serif;color:var(--ink);background:var(--page)}
.canvas{position:relative;width:730px;height:1200px;overflow:hidden;background:var(--page)}
a{color:var(--link);text-decoration:none}
.abs{position:absolute}

/* header */
.site-header{position:absolute;left:0;top:0;width:730px;height:58px;background:var(--blue)}
.site-title{position:absolute;left:110px;top:10px;font-family:"Ubuntu",sans-serif;font-size:19px;color:#fff;font-weight:400;letter-spacing:.2px}
.tagline{position:absolute;left:110px;top:41px;font-size:7.3px;color:#e3f0fa}
.main-nav{position:absolute;left:0;top:58px;width:730px;height:30px;background:linear-gradient(#f3574e,#e9463e);border-bottom:1px solid #c93a33}
.main-nav ul{list-style:none;position:absolute;left:105px;top:0;display:flex;height:30px}
.main-nav li{font-size:7.6px;color:#fff;padding:0 11px;line-height:30px}
.main-nav li.active{background:#2b2b2b;padding:0 13px}

/* cards */
.card{position:absolute;background:var(--card);border:1px solid #d4d4d4;box-shadow:0 1px 2px rgba(0,0,0,.08)}

/* slider */
.slider{left:105px;top:111px;width:521px;height:206px}
.slide-photo{position:absolute;left:5px;top:7px;width:509px;height:192px;background:radial-gradient(circle at 45% 45%,#3e6f98 0%,#1a3650 40%,#0b1a28 80%)}
.slide-panel{position:absolute;left:440px;top:118px;width:179px;height:192px;background:rgba(30,30,30,.78);padding:13px 8px 0 8px;color:#fff}
.slide-panel h2{font-size:8px;font-weight:600;line-height:15.5px}
.slide-panel .meta{font-size:6px;color:#ddd}
.slide-panel p{font-size:6.6px;line-height:12.5px;margin-top:4px}
.btn-red{display:inline-block;background:var(--red);color:#fff;font-size:6.6px;text-transform:uppercase;padding:0 13px;line-height:18px}
.slide-panel .btn-red{margin-top:9px}
.dots{position:absolute;right:25px;top:289px;display:flex;gap:3px}
.dots span{width:5px;height:5px;border-radius:50%;background:#fff}
.dots span.on{background:transparent;border:1px solid #fff}
.slide-arrow{position:absolute;top:286px;width:14px;height:13px;display:flex;align-items:center;justify-content:center}
.slide-arrow.prev{left:120px;background:#111}
.slide-arrow.next{left:137px;background:var(--red)}

/* posts */
.posts{left:105px;top:331px;width:348px;height:735px}
.post-photo{position:absolute;left:5px;width:337px;height:141px}
.photo-tablet{top:8px;background:linear-gradient(135deg,#5a6d7e 0%,#c8d3dc 45%,#e9eef2 70%,#8fa1b1 100%)}
.photo-helix{top:296px;background:radial-gradient(circle at 55% 45%,#3b6270 0%,#1a2e38 50%,#0a1216 100%)}
.rating{position:absolute;width:69px;height:17px;background:var(--red);display:flex;align-items:center;justify-content:center;gap:2px}
.rating svg{width:10px;height:10px}
.post-title{position:absolute;left:9px;width:330px;font-size:10.2px;font-weight:400;color:#222;line-height:16px}
.post-meta{position:absolute;left:9px;width:330px;height:10px;font-size:6.3px;display:flex;align-items:center}
.post-meta .item{display:flex;align-items:center;gap:3px;margin-right:13px;color:var(--link)}
.post-meta .share{margin-left:auto;display:flex;align-items:center;gap:5px;color:#444}
.share i{display:block;width:6px;height:6px;border-radius:50%;background:#9a9a9a}
.rule{position:absolute;left:5px;width:337px;height:1px;background:var(--line)}
.post-body{position:absolute;left:9px;width:330px;font-size:6.9px;line-height:12.45px;color:#444}
.post-body .more{color:var(--red)}
.band{position:absolute;left:5px;width:337px;height:4px;background:repeating-linear-gradient(135deg,#ddd 0 1px,#fff 1px 3px)}

/* sidebar */
.sidebar{left:462px;top:331px;width:164px;height:735px}
.search{position:absolute;left:8px;top:9px;width:148px;height:22px;border:1px solid #ccc;background:#fff}
.search span{position:absolute;left:6px;top:6px;font-size:6px;color:#aaa}
.search .go{position:absolute;right:-1px;top:-1px;width:32px;height:22px;background:var(--blue);display:flex;align-items:center;justify-content:center}
.widget-title{position:absolute;left:8px;width:148px;height:16px;background:repeating-linear-gradient(135deg,#ddd 0 1px,#fff 1px 3px)}
.widget-title span{display:inline-block;height:16px;line-height:16px;background:var(--blue);color:#fff;font-size:7.2px;padding:0 6px;text-transform:uppercase}
.mini-post{position:absolute;left:8px;width:150px;height:34px}
.mini-thumb{position:absolute;left:0;top:2px;width:40px;height:32px}
.mini-text{position:absolute;left:44px;top:0;width:108px}
.mini-text h3{font-size:7px;font-weight:400;line-height:12.4px;color:#222}
.mini-text .meta{font-size:5.4px;color:#444;margin-top:1px}
.follow{position:absolute;left:8px;display:flex;align-items:center;gap:6px;font-size:7.2px}
.follow i{display:block;width:20px;height:20px;border-radius:4px}
.input{position:absolute;left:8px;width:148px;height:24px;border:2px solid #ddd;background:#fafafa;font-size:7px;color:#777;padding-left:7px;line-height:20px}
.subscribe{position:absolute;left:8px;top:704px;height:18px;padding:0 11px}

/* pagination */
.pager{position:absolute;left:105px;top:1077px;display:flex;gap:9px}
.pager span{width:23px;height:22px;background:var(--blue);color:#fff;font-size:7px;display:flex;align-items:center;justify-content:center}
.pager span.current{background:var(--red)}

/* footer */
.site-footer{position:absolute;left:0;top:1112px;width:730px;height:88px;background:var(--footer);border-top:2px solid var(--blue)}
.footer-links{position:absolute;top:17px;left:0;width:730px;display:flex;justify-content:center;gap:15px;font-size:7.3px;color:#ddd}
.footer-social{position:absolute;top:41px;left:0;width:730px;display:flex;justify-content:center;gap:10px}
.footer-social i{display:block;width:21px;height:21px;border-radius:50%;border:2px solid #fff}
.copyright{position:absolute;top:73px;left:0;width:730px;text-align:center;font-size:5.8px;color:#ccc}
</style>
</head>
<body>
<svg width="0" height="0" style="position:absolute">
  <defs>
    <symbol id="star" viewBox="0 0 10 10"><path d="M5 .4l1.4 3 3.2.3-2.4 2.2.7 3.2L5 7.5 2.1 9.1l.7-3.2L.4 3.7l3.2-.3z"/></symbol>
  </defs>
</svg>
<div class="canvas">

  <header class="site-header">
    <div class="site-title">Hollow Peak Desk</div>
    <div class="tagline">Rowan talks business. Best practices, articles and tips and about small business in the United States.</div>
  </header>
  <nav class="main-nav">
    <ul>
      <li class="active">Home</li><li>Small Business</li><li>Technology</li><li>About Rowan</li><li>Contact</li>
    </ul>
  </nav>

  <section class="card slider">
    <div class="slide-photo" role="img" aria-label="Hand touching glowing digital communication icons"></div>
  </section>
  <div class="slide-panel">
    <h2>Comparing Direct Mail to Dealbloom – By the Numbers</h2>
    <div class="meta">Posted on <a>March 6, 2014</a> by <a>Rowan</a></div>
    <p>Unhappy with the results of a direct mail (snail mail) campaign, I decided to compare the results to a Dealbloom campaign...</p>
    <span class="btn-red">Read More</span>
  </div>
  <div class="slide-arrow prev"><svg width="6" height="7" viewBox="0 0 6 7"><path d="M4.5 .5L1.5 3.5l3 3" stroke="#fff" fill="none" stroke-width="1.4"/></svg></div>
  <div class="slide-arrow next"><svg width="6" height="7" viewBox="0 0 6 7"><path d="M1.5 .5l3 3-3 3" stroke="#fff" fill="none" stroke-width="1.4"/></svg></div>
  <div class="dots"><span></span><span class="on"></span><span></span><span></span></div>

  <main class="card posts">
    <!-- post 1 -->
    <div class="post-photo photo-tablet" role="img" aria-label="Hands using a tablet showing a chart"></div>
    <div class="rating" style="left:273px;top:132px">
      <svg fill="var(--star)"><use href="#star"/></svg><svg fill="var(--star)"><use href="#star"/></svg><svg fill="var(--star)"><use href="#star"/></svg><svg fill="var(--star)"><use href="#star"/></svg><svg fill="#111"><use href="#star"/></svg>
    </div>
    <h2 class="post-title" style="top:160px">Comparing Direct Mail to Dealbloom – By the Numbers</h2>
    <div class="post-meta" style="top:187px">
      <span class="item"><svg width="7" height="6"><rect x=".5" y=".5" width="6" height="5" fill="none" stroke="#777"/><rect x=".5" y=".5" width="6" height="1.5" fill="#777"/></svg>March 6, 2014</span>
      <span class="item"><svg width="6" height="7"><circle cx="3" cy="2" r="1.7" fill="#777"/><path d="M0 7a3 3 0 0 1 6 0z" fill="#777"/></svg>Rowan</span>
      <span class="item"><svg width="7" height="6"><path d="M0 0h7v4H3L1 6V4H0z" fill="#777"/></svg>Leave a comment</span>
      <span class="share">Share On :<i></i><i></i><i></i><i></i></span>
    </div>
    <div class="rule" style="top:203px"></div>
    <p class="post-body" style="top:210px">Unhappy with the results of a direct mail (snail mail) campaign, I decided to compare the results to a Dealbloom campaign. I compared both the cost of the respective campaigns, the revenue generated, the customers acquired and customer retention. Unhappy with the results of a direct mail (snail mail) campaign, I decided to compare the results to a Dealbloom campaign. I compared both the cost of the respective campaigns, the revenue generated, the customers acquired and customer retention<span class="more">....</span></p>
    <div class="band" style="top:281px"></div>

    <!-- post 2 -->
    <div class="post-photo photo-helix" role="img" aria-label="Abstract digital helix and reaching hand"></div>
    <div class="rating" style="left:273px;top:420px">
      <svg fill="var(--star)"><use href="#star"/></svg><svg fill="var(--star)"><use href="#star"/></svg><svg fill="var(--star)"><use href="#star"/></svg><svg fill="var(--star)"><use href="#star"/></svg><svg fill="#111"><use href="#star"/></svg>
    </div>
    <h2 class="post-title" style="top:448px">Finally Dumping Loopchat on Orbit OS – Any Recommendations for an SMS App?</h2>
    <div class="post-meta" style="top:486px">
      <span class="item"><svg width="7" height="6"><rect x=".5" y=".5" width="6" height="5" fill="none" stroke="#777"/><rect x=".5" y=".5" width="6" height="1.5" fill="#777"/></svg>March 6, 2014</span>
      <span class="item"><svg width="6" height="7"><circle cx="3" cy="2" r="1.7" fill="#777"/><path d="M0 7a3 3 0 0 1 6 0z" fill="#777"/></svg>Rowan</span>
      <span class="item"><svg width="7" height="6"><path d="M0 0h7v4H3L1 6V4H0z" fill="#777"/></svg>Leave a comment</span>
      <span class="share">Share On :<i></i><i></i><i></i><i></i></span>
    </div>
    <div class="rule" style="top:502px"></div>
    <p class="post-body" style="top:509px">Unhappy with the results of a direct mail (snail mail) campaign, I decided to compare the results to a Dealbloom campaign. I compared both the cost of the respective campaigns, the revenue generated, the customers acquired and customer retention. Unhappy with the results of a direct mail (snail mail) campaign, I decided to compare the results to a Dealbloom campaign. I compared both the cost of the respective campaigns, the revenue generated, the customers acquired and customer retention<span class="more">....</span></p>
    <div class="band" style="top:580px"></div>

    <!-- post 3 -->
    <h2 class="post-title" style="top:595px">Comparing Direct Mail to Dealbloom – By the Numbers</h2>
    <div class="rating" style="left:273px;top:595px">
      <svg fill="var(--star)"><use href="#star"/></svg><svg fill="var(--star)"><use href="#star"/></svg><svg fill="var(--star)"><use href="#star"/></svg><svg fill="var(--star)"><use href="#star"/></svg><svg fill="#111"><use href="#star"/></svg>
    </div>
    <div class="post-meta" style="top:621px">
      <span class="item"><svg width="7" height="6"><rect x=".5" y=".5" width="6" height="5" fill="none" stroke="#777"/><rect x=".5" y=".5" width="6" height="1.5" fill="#777"/></svg>March 6, 2014</span>
      <span class="item"><svg width="6" height="7"><circle cx="3" cy="2" r="1.7" fill="#777"/><path d="M0 7a3 3 0 0 1 6 0z" fill="#777"/></svg>Rowan</span>
      <span class="item"><svg width="7" height="6"><path d="M0 0h7v4H3L1 6V4H0z" fill="#777"/></svg>Leave a comment</span>
      <span class="share">Share On :<i></i><i></i><i></i><i></i></span>
    </div>
    <div class="rule" style="top:637px"></div>
    <p class="post-body" style="top:645px">Unhappy with the results of a direct mail (snail mail) campaign, I decided to compare the results to a Dealbloom campaign. I compared both the cost of the respective campaigns, the revenue generated, the customers acquired and customer retention. Unhappy with the results of a direct mail (snail mail) campaign, I decided to compare the results to a Dealbloom campaign. I compared both the cost of the respective campaigns, the revenue generated, the customers acquired and customer retention....</p>
    <div class="band" style="top:716px"></div>
  </main>

  <aside class="card sidebar">
    <div class="search"><span>Search Here....</span>
      <div class="go"><svg width="11" height="11" viewBox="0 0 11 11"><circle cx="4.5" cy="4.5" r="3.3" fill="none" stroke="#fff" stroke-width="1.5"/><path d="M7 7l3.2 3.2" stroke="#fff" stroke-width="1.7"/></svg></div>
    </div>

    <div class="widget-title" style="top:51px"><span>Recent Posts</span></div>
    <div class="mini-post" style="top:79px"><div class="mini-thumb" role="img" aria-label="Silver car" style="background:linear-gradient(135deg,#2d4f7a,#a9b9c9)"></div><div class="mini-text"><h3>Morbi vulputate egestas sem, eu cursus...</h3><div class="meta">Posted on <a>March 6, 2014</a> by <a>Rowan</a></div></div></div>
    <div class="mini-post" style="top:121px"><div class="mini-thumb" role="img" aria-label="Globe on a green field" style="background:linear-gradient(#2f7fd0,#55a83c)"></div><div class="mini-text"><h3>Morbi vulputate egestas sem, eu cursus...</h3><div class="meta">Posted on <a>March 6, 2014</a> by <a>Rowan</a></div></div></div>
    <div class="mini-post" style="top:163px"><div class="mini-thumb" role="img" aria-label="Colourful cartoon group" style="background:linear-gradient(135deg,#c88a3a,#7a4a2a)"></div><div class="mini-text"><h3>Morbi vulputate egestas sem, eu cursus...</h3><div class="meta">Posted on <a>March 6, 2014</a> by <a>Rowan</a></div></div></div>
    <div class="mini-post" style="top:204px"><div class="mini-thumb" role="img" aria-label="Light bulb with glowing line art" style="background:radial-gradient(circle,#9bb4d8,#2a3f66)"></div><div class="mini-text"><h3>Morbi vulputate egestas sem, eu cursus...</h3><div class="meta">Posted on <a>March 6, 2014</a> by <a>Rowan</a></div></div></div>
    <div class="mini-post" style="top:246px"><div class="mini-thumb" role="img" aria-label="Robot figure on teal background" style="background:linear-gradient(135deg,#1d5a63,#8fc7c6)"></div><div class="mini-text"><h3>Morbi vulputate egestas sem, eu cursus...</h3><div class="meta">Posted on <a>March 6, 2014</a> by <a>Rowan</a></div></div></div>

    <div class="widget-title" style="top:297px"><span>Top Posts</span></div>
    <div class="mini-post" style="top:325px"><div class="mini-thumb" role="img" aria-label="Glass office tower" style="background:linear-gradient(135deg,#5d8fc2,#dfeaf5)"></div><div class="mini-text"><h3>Morbi vulputate egestas sem, eu cursus...</h3><div class="meta">Posted on <a>March 6, 2014</a> by <a>Rowan</a></div></div></div>
    <div class="mini-post" style="top:367px"><div class="mini-thumb" role="img" aria-label="Road with a highway sign" style="background:linear-gradient(#7d96b3,#5f6a4a)"></div><div class="mini-text"><h3>Morbi vulputate egestas sem, eu cursus...</h3><div class="meta">Posted on <a>March 6, 2014</a> by <a>Rowan</a></div></div></div>
    <div class="mini-post" style="top:409px"><div class="mini-thumb" role="img" aria-label="Yellow promotional graphic" style="background:#f6c51b"></div><div class="mini-text"><h3>Morbi vulputate egestas sem, eu cursus...</h3><div class="meta">Posted on <a>March 6, 2014</a> by <a>Rowan</a></div></div></div>

    <div class="widget-title" style="top:453px"><span>Follow On</span></div>
    <div class="follow" style="top:483px;color:#f28a1d"><i style="background:#f28a1d"></i>RSS Feed</div>
    <div class="follow" style="top:509px;color:#3b5a9a"><i style="background:#3b5a9a"></i>Friendwall</div>
    <div class="follow" style="top:535px;color:#2ca7e0"><i style="background:#2ca7e0"></i>Chirpline</div>
    <div class="follow" style="top:561px;color:#d23e2b"><i style="background:#d23e2b"></i>Circleplus</div>

    <div class="widget-title" style="top:600px"><span>Newsletter Signup</span></div>
    <div class="input" style="top:630px">Name</div>
    <div class="input" style="top:667px">Mail Address</div>
    <span class="btn-red subscribe">Subscribe</span>
  </aside>

  <div class="pager"><span>1</span><span class="current">2</span><span>3</span><span>....</span><span>29</span></div>

  <footer class="site-footer">
    <div class="footer-links"><span>Terms of Service</span><span>Privacy Policy</span><span>Events</span><span>Contact</span><span>Blog</span><span>Sitemap</span></div>
    <div class="footer-social">
      <i style="background:#3b5a9a"></i><i style="background:#2ca7e0"></i><i style="background:#c9232d"></i><i style="background:#d23e2b"></i><i style="background:#f06a1d"></i>
    </div>
    <div class="copyright">copyright@ 2014 .all right reserved.</div>
  </footer>
</div>
</body>
</html>
```